Need Business Card for our Real Estate Business with Sales Executive's Picture

PANTONE 484 C ( RED)

PANTONE 2766 C ( BLUE

Industry/Entity Type

Real Estate

Contact Information for Business Card

Name, Mobile, email, & picture of Person
Agency Phone, address, Web address

Requirements
Must have
• Our Logo Colours, Agent Picture,

```html
<!DOCTYPE html>
<html lang="en">
<head>
<meta charset="utf-8">
<title>Meridian Real Estate – Business Card</title>
<link rel="stylesheet" href="https://fonts.googleapis.com/css2?family=Cinzel:wght@500;600&family=Open+Sans:wght@400;700&display=swap">
<style>
  :root {
    --navy: #0b1538;
    --navy-line: #c9cfe0;
    --red: #7a1c22;
    --paper-top: #ffffff;
    --paper-bottom: #e4e6ea;
    --stage: #8d8f93;
    --muted: #7d8499;
    --white: #ffffff;
  }
  * { box-sizing: border-box; margin: 0; padding: 0; }
  html, body { width: 1200px; height: 1200px; overflow: hidden; }
  body {
    background: var(--stage);
    font-family: "Open Sans", sans-serif;
    display: flex;
    flex-direction: column;
    align-items: center;
    justify-content: center;
    gap: 56px;
  }
  .card {
    position: relative;
    width: 900px;
    height: 514px;
    overflow: hidden;
    box-shadow: 0 6px 14px rgba(0,0,0,.35);
  }

  /* Front */
  .card--front { background: var(--navy); }
  .front__paper {
    position: absolute; left: 0; top: 0; width: 100%; height: 296px;
    background: linear-gradient(180deg, var(--paper-top), var(--paper-bottom));
  }
  .brand {
    position: absolute; display: flex; align-items: center; gap: 14px;
    font-family: "Cinzel", serif; font-weight: 600; letter-spacing: 2px;
  }
  .brand__mark { width: 16px; height: 16px; background: var(--red); flex: none; }
  .card--front .brand { left: 44px; top: 124px; font-size: 30px; color: var(--navy); }
  .agent-photo {
    position: absolute; right: 26px; top: 20px; width: 300px; height: 494px;
    background: linear-gradient(180deg, #d9dce3 0%, #3f5fae 40%, #1f3a8a 100%);
  }
  .agent {
    position: absolute; left: 48px; top: 326px; color: var(--white); width: 560px;
  }
  .agent__name {
    font-family: "Cinzel", serif; font-weight: 600; font-size: 38px; letter-spacing: 1px;
  }
  .agent__role {
    display: flex; align-items: center; gap: 12px; margin-top: 2px;
    font-size: 16px; letter-spacing: 2px; color: var(--muted);
  }
  .agent__role::after { content: ""; flex: 1; height: 2px; background: var(--navy-line); }
  .contact { display: flex; align-items: center; gap: 16px; }
  .contact svg { width: 22px; height: 22px; flex: none; }
  .contact--phone { margin-top: 16px; font-size: 29px; font-weight: 700; }
  .contact--email { margin-top: 6px; font-size: 24px; }

  /* Back */
  .card--back { background: var(--navy); color: var(--white); text-align: center; }
  .card--back .brand {
    left: 0; right: 0; top: 196px; justify-content: center; font-size: 40px; color: var(--white);
  }
  .back__contacts { position: absolute; left: 0; right: 0; top: 390px; font-size: 24px; line-height: 44px; }
  .back__row { display: flex; justify-content: center; gap: 36px; }
  .back__row .contact { gap: 10px; }
</style>
</head>
<body>

<section class="card card--front">
  <div class="front__paper"></div>
  <div class="brand"><span class="brand__mark"></span>Meridian Real Estate</div>
  <div class="agent-photo" role="img" aria-label="Portrait photo of the agent in a blue suit"></div>
  <div class="agent">
    <div class="agent__name">Arjun Mehta</div>
    <div class="agent__role">DIRECTOR</div>
    <div class="contact contact--phone">
      <svg viewBox="0 0 24 24" fill="none" stroke="#fff" stroke-width="2.4"><rect x="6" y="2" width="12" height="20" rx="2"/><line x1="11" y1="18" x2="13" y2="18"/></svg>
      (000) 000-0000
    </div>
    <div class="contact contact--email">
      <svg viewBox="0 0 24 24" fill="#fff"><path d="M2 9l10-6 10 6v12H2z"/><path d="M3 10l9 6 9-6" stroke="#0b1538" stroke-width="1.6" fill="none"/></svg>
      arjun.mehta@email.com
    </div>
  </div>
</section>

<section class="card card--back">
  <div class="brand"><span class="brand__mark"></span>Meridian Real Estate</div>
  <div class="back__contacts">
    <div class="back__row">
      <span class="contact">
        <svg viewBox="0 0 24 24" fill="#fff"><path d="M2 9c0-3 4-5 10-5s10 2 10 5l-1 2-4-1V8c-3-1-7-1-10 0v2l-4 1z"/><path d="M6 13h12l2 7H4z"/><circle cx="12" cy="16.5" r="2" fill="#0b1538"/></svg>
        (000) 000-0000
      </span>
      <span class="contact">
        <svg viewBox="0 0 24 24" fill="#fff"><path d="M12 3l10 9h-3v9h-5v-6h-4v6H5v-9H2z"/></svg>
        www.domain.com
      </span>
    </div>
    <div>Shop 9/118 Harlow RD, Westbrook, VIC 3030</div>
  </div>
</section>

</body>
</html>
```